Business Card design for insurance broker in Denver, CO, USA

I need a business card designed using this logo that was just created. We sell life and disability income insurance to US consumers.
Looking for a professionally designed card to make use of the logo and have something to hand to prospects or new business referral sources. The card could be white, gray, black or whatever you would recommend.

Target Market(s)

US Consumers and other financial professionals that I partner with.

Industry/Entity Type

Insurance Broker

Contact Information for Business Card

Owen T. Farrow, CLU, LUTCF (please note that CLU should have a superscript R in a circle for registered trademark)
President
phone (303) 555-0187
email owen@keelbrookcover.example
4620 W. Halvern Rd, Suite 300, Greenwood Village, CO 80111
Somewhere fit in a tagline saying "Your partner for LIFE, long term CARE, and DISABILITY COVERAGE" (maybe the back if it doesn't fit on the front, your call)

Font styles to use
Sans Serif

Requirements
Must have
• Must have logo in correct blue and gray colors, my name, address, phone, email. Order and placement determined by the designer.
• I just want something that looks a more professional than what I could have done using the business card designer tool on pixelbazaar.example or QuillPress, or any other do-it-yourself tool
• A regular rectangular business card with square corners is preferred
Nice to have
• I included the logos of 2 organizations I belong to (GKLS and WOBCE). They should be small, but visible on the back only. If it doesn’t look good, this is not a requirement, feel free to drop it.
Should not have
• Do not add any colors not already in the logo, except use of black and whites which are okay. If you use the logo on the back and want to make that in all black, gray or white, that may be okay as well.

```html
<!DOCTYPE html>
<html lang="en">
<head>
<meta charset="utf-8">
<title>Keelbrook Cover Solutions – Business Card</title>
<link rel="stylesheet" href="https://fonts.googleapis.com/css2?family=Montserrat:wght@400;500;600;700&display=swap">
<style>
  :root {
    --stage: #3a3a3c;
    --card-dark: #2a292b;
    --card-light: #ffffff;
    --brand-blue: #1f86cc;
    --band-gray: #a3a3a5;
    --ink-gray: #7d7d7f;
    --white: #ffffff;
  }
  * { box-sizing: border-box; margin: 0; padding: 0; }
  html, body { width: 1200px; height: 900px; overflow: hidden; }
  body {
    background: var(--stage);
    font-family: "Montserrat", Arial, sans-serif;
    position: relative;
  }
  .card {
    position: absolute;
    left: 240px;
    width: 720px;
    height: 400px;
    overflow: hidden;
    box-shadow: 0 10px 30px rgba(0,0,0,.45);
  }
  .card-back { top: 40px; background: var(--card-dark); }
  .card-front { top: 470px; background: var(--card-light); }
  .card-waves { position: absolute; inset: 0; width: 100%; height: 100%; }

  .brand {
    position: absolute;
    color: var(--brand-blue);
    font-weight: 600;
    text-transform: uppercase;
    line-height: 1.1;
  }
  .brand span { display: block; }
  .card-back .brand { left: 0; right: 0; top: 70px; text-align: center; font-size: 32px; }
  .card-front .brand { right: 40px; top: 130px; font-size: 22px; }

  .tagline {
    position: absolute;
    right: 30px; bottom: 42px;
    width: 360px;
    color: var(--white);
    font-size: 14px;
    font-weight: 500;
    line-height: 1.4;
  }

  .flag {
    position: absolute; left: 0; top: 42px;
    width: 0; height: 0;
    border-top: 9px solid transparent;
    border-bottom: 9px solid transparent;
    border-left: 16px solid var(--brand-blue);
  }
  .person { position: absolute; left: 40px; top: 38px; }
  .person-name {
    color: var(--ink-gray);
    font-size: 21px; font-weight: 700;
    letter-spacing: .5px;
    text-transform: uppercase;
  }
  .person-creds { color: var(--brand-blue); font-size: 14px; font-weight: 600; margin-left: 4px; }
  .person-creds sup { font-size: 9px; }
  .person-title { color: var(--brand-blue); font-size: 15px; font-weight: 500; margin-top: 2px; }

  .contact-list { position: absolute; left: 32px; top: 130px; list-style: none; }
  .contact-list li {
    display: flex; align-items: center; gap: 12px;
    color: var(--ink-gray);
    font-size: 16px;
    margin-bottom: 9px;
  }
  .contact-list svg { width: 18px; height: 18px; fill: var(--brand-blue); flex: none; }

  .address {
    position: absolute; left: 36px; bottom: 34px;
    display: flex; gap: 14px;
    color: var(--white);
    font-size: 16px; font-weight: 500;
    line-height: 1.45;
  }
  .address svg { width: 16px; height: 20px; fill: var(--white); margin-top: 2px; flex: none; }
</style>
</head>
<body>

<section class="card card-back" aria-label="Card back">
  <svg class="card-waves" viewBox="0 0 720 400" preserveAspectRatio="none" aria-hidden="true">
    <path fill="var(--band-gray)" d="M0,240 C150,282 300,292 420,292 C560,292 650,272 720,300 L720,400 L0,400Z"/>
    <path fill="var(--brand-blue)" d="M0,192 C120,248 300,284 460,290 C300,272 120,238 0,214Z"/>
    <path fill="var(--card-dark)" d="M410,300 C540,278 660,266 720,330 L720,318 C650,280 540,284 410,300Z"/>
  </svg>
  <p class="brand"><span>Keelbrook</span><span>Cover Solutions</span></p>
  <p class="tagline">Your partner for LIFE, long term CARE, and DISABILITY COVERAGE</p>
</section>

<section class="card card-front" aria-label="Card front">
  <svg class="card-waves" viewBox="0 0 720 400" preserveAspectRatio="none" aria-hidden="true">
    <path fill="var(--band-gray)" d="M0,250 C180,240 320,300 420,350 C520,395 640,382 720,372 L720,400 L0,400Z"/>
    <path fill="var(--white)" d="M60,262 C200,246 310,288 390,336 C290,292 170,274 60,262Z"/>
    <path fill="var(--white)" d="M372,330 C480,384 620,378 720,336 L720,350 C620,392 480,394 372,330Z"/>
    <path fill="var(--brand-blue)" d="M392,346 C490,390 620,384 720,348 L720,364 C620,398 490,398 392,346Z"/>
  </svg>

  <span class="flag" aria-hidden="true"></span>
  <div class="person">
    <p class="person-name">Owen T. Farrow<span class="person-creds">CLU<sup>®</sup>, LUTCF</span></p>
    <p class="person-title">President</p>
  </div>

  <ul class="contact-list">
    <li>
      <svg viewBox="0 0 24 24" aria-hidden="true"><path d="M6.6 10.8a15.1 15.1 0 0 0 6.6 6.6l2.2-2.2c.3-.3.7-.4 1-.2 1.1.4 2.3.6 3.6.6.6 0 1 .4 1 1V20c0 .6-.4 1-1 1A17 17 0 0 1 3 4c0-.6.4-1 1-1h3.5c.6 0 1 .4 1 1 0 1.3.2 2.5.6 3.6.1.3 0 .7-.2 1z"/></svg>
      (555) 201-0187
    </li>
    <li>
      <svg viewBox="0 0 24 24" aria-hidden="true"><path d="M2 5h20v14H2z M3 6l9 7 9-7" fill="none" stroke="var(--brand-blue)" stroke-width="2"/><path d="M2 5h20l-10 8z"/></svg>
      owen@keelbrookcover.example
    </li>
    <li>
      <svg viewBox="0 0 24 24" aria-hidden="true"><circle cx="12" cy="12" r="10"/><path d="M2 12h20M12 2c3 3 3 17 0 20M12 2c-3 3-3 17 0 20M4 7h16M4 17h16" fill="none" stroke="var(--white)" stroke-width="1.3"/></svg>
      www.keelbrookcover.example
    </li>
  </ul>

  <p class="brand"><span>Keelbrook</span><span>Cover Solutions</span></p>

  <div class="address">
    <svg viewBox="0 0 16 20" aria-hidden="true"><path d="M8 0a7 7 0 0 0-7 7c0 5 7 13 7 13s7-8 7-13a7 7 0 0 0-7-7zm0 10a3 3 0 1 1 0-6 3 3 0 0 1 0 6z"/></svg>
    <p>4620 W. Halvern Rd, Suite 300<br>Larkmoor Springs, CO 80999</p>
  </div>
</section>

</body>
</html>
```